Business Card Design

I am an Event and Wedding Planner in need of an eye catching business card featuring my logo (attached), my contact details, and my company tagline (Making every celebration glow with wonder...) I would like the tagline in font similar the logo's font.
Updates
I have just noticed that my logo has a misspelling so for the final design, I will be uploading a corrected logo as soon as I have it.
My apologies.
Reason: Waiting on a corrected logo...Lantern is misspelled and it should say Weddings not Wedding
The logo has been corrected so now Lantern is spelled correctly and it says Weddings instead of Wedding. Please use Edwardian Script ITC as the font for the tagline so it will match the logo. Thank you for your patience.
Target Market(s)
Engaged couples and people hosting milestone celebrations. 25-50 years old, predominately female
Industry/Entity Type
Business
Contact Information for Business Card
Rosalind Merrow, Event Manager / Owner, Mobile: 0491 868 254, Email: rosalind@velvetlanternco.com.au, www.velvetlanternco.com.au, Making every celebration glow with wonder...

```html
<!DOCTYPE html>
<html lang="en">
<head>
<meta charset="utf-8">
<title>Velvet Lantern Co. – Business Card</title>
<link rel="stylesheet" href="https://fonts.googleapis.com/css2?family=Pinyon+Script&family=Exo+2:wght@400;500&display=swap">
<style>
  :root {
    --page: #e4e4e4;
    --card: #ffffff;
    --ink: #111111;
    --panel: #0c0c0c;
    --panel-text: #f4f4f4;
    --accent: #c8423e;
    --rule: #8a8a8a;
  }
  * { box-sizing: border-box; margin: 0; padding: 0; }
  html, body { width: 1200px; height: 898px; overflow: hidden; }
  body { background: var(--page); position: relative; }

  .card {
    position: absolute;
    width: 560px;
    height: 320px;
    background: var(--card);
    box-shadow: 0 10px 28px rgba(0,0,0,.22);
    overflow: hidden;
  }
  .card--front { left: 70px; top: 130px; }
  .card--back { left: 570px; top: 450px; }

  .brand { position: absolute; text-align: center; color: var(--ink); }
  .brand__mark {
    display: inline-flex;
    align-items: center;
    gap: 10px;
    font-family: "Exo 2", sans-serif;
    font-weight: 500;
    letter-spacing: .08em;
    white-space: nowrap;
  }
  .brand__dot { border-radius: 50%; background: var(--accent); flex: none; }
  .brand__rule { height: 1px; background: var(--rule); margin: 12px auto 8px; width: 88%; }
  .tagline {
    font-family: "Pinyon Script", cursive;
    font-weight: 400;
    line-height: 1.25;
  }

  .card--front .brand { left: 0; right: 0; top: 110px; }
  .card--front .brand__mark { font-size: 32px; }
  .card--front .brand__dot { width: 14px; height: 14px; }
  .card--front .tagline { font-size: 28px; }

  .edge-stripes { position: absolute; left: 0; top: 0; bottom: 0; width: 22px; }
  .edge-stripes .black { position: absolute; left: 0; top: 0; bottom: 0; width: 8px; background: var(--panel); }
  .edge-stripes .red { position: absolute; left: 8px; top: 120px; bottom: 0; width: 12px; background: var(--accent); }

  .card--back .brand { left: 34px; width: 290px; top: 108px; }
  .card--back .brand__mark { font-size: 22px; gap: 8px; }
  .card--back .brand__dot { width: 10px; height: 10px; }
  .card--back .tagline { font-size: 23px; }

  .contact-panel {
    position: absolute;
    right: 0; top: 0; bottom: 0;
    width: 220px;
    background: var(--panel);
    color: var(--panel-text);
    font-family: "Exo 2", sans-serif;
    text-align: right;
    padding: 26px 18px 20px 10px;
  }
  .person__name { font-size: 15px; letter-spacing: .12em; font-weight: 500; }
  .person__title { font-size: 10px; letter-spacing: .1em; margin-top: 3px; }
  .address { font-size: 11px; line-height: 1.55; margin-top: 36px; letter-spacing: .03em; }
  .details { list-style: none; margin-top: 28px; font-size: 10.5px; line-height: 1.9; letter-spacing: .03em; }
  .details li { display: flex; justify-content: flex-end; align-items: center; gap: 7px; white-space: nowrap; }
  .details svg { width: 11px; height: 11px; flex: none; }
  .details .web { font-size: 9.5px; }
</style>
</head>
<body>

<section class="card card--front" aria-label="Card front">
  <div class="brand">
    <div class="brand__mark">Velvet Lantern Co.<span class="brand__dot"></span></div>
    <div class="brand__rule"></div>
    <p class="tagline">Making every celebration glow with wonder...</p>
  </div>
</section>

<section class="card card--back" aria-label="Card back">
  <div class="edge-stripes"><span class="black"></span><span class="red"></span></div>

  <div class="brand">
    <div class="brand__mark">Velvet Lantern Co.<span class="brand__dot"></span></div>
    <div class="brand__rule"></div>
    <p class="tagline">Making every celebration<br>glow with wonder...</p>
  </div>

  <div class="contact-panel">
    <div class="person__name">ROSALIND MERROW</div>
    <div class="person__title">EVENT MANAGER / OWNER</div>

    <div class="address">14 Harbour Lane,<br>Level 2 Wattle Street W.</div>

    <ul class="details">
      <li>0491 868 254
        <svg viewBox="0 0 24 24" fill="currentColor"><path d="M6.6 10.8a15 15 0 0 0 6.6 6.6l2.2-2.2a1 1 0 0 1 1-.25 11.4 11.4 0 0 0 3.6.6 1 1 0 0 1 1 1V20a1 1 0 0 1-1 1A17 17 0 0 1 3 4a1 1 0 0 1 1-1h3.5a1 1 0 0 1 1 1c0 1.250.2 2.45.57 3.57a1 1 0 0 1-.25 1z"/></svg>
      </li>
      <li>0491 868 255
        <svg viewBox="0 0 24 24" fill="none" stroke="currentColor" stroke-width="2"><rect x="6" y="2" width="12" height="20" rx="2"/><line x1="11" y1="18" x2="13" y2="18"/></svg>
      </li>
      <li>0491 868 256
        <svg viewBox="0 0 24 24" fill="currentColor"><rect x="3" y="9" width="18" height="11" rx="1"/><rect x="7" y="3" width="10" height="5"/></svg>
      </li>
      <li>rosalind@velvetlanternco.com.au
        <svg viewBox="0 0 24 24" fill="none" stroke="currentColor" stroke-width="2"><rect x="2" y="5" width="20" height="14" rx="1"/><path d="M2 6l10 7 10-7"/></svg>
      </li>
      <li class="web">www.velvetlanternco.com.au
        <svg viewBox="0 0 24 24" fill="none" stroke="currentColor" stroke-width="2"><circle cx="12" cy="12" r="10"/><path d="M2 12h20M12 2a15 15 0 0 1 0 20M12 2a15 15 0 0 0 0 20"/></svg>
      </li>
    </ul>
  </div>
</section>

</body>
</html>
```